New Business Card Design Project

We require a business card design for Vexalund, a newly established Indian company.
Our focus is on the development, manufacturing, and export of a diverse array of pharmaceutical products on a global scale. The card should convey a professional appearance, as our primary markets are in Africa, China, and Southeast Asian nations.
We envision a two-sided business card, with the reverse side dedicated to a logo set against a solid color or an elegantly designed pattern. The corners should be rounded. We would appreciate seeing both horizontal and vertical design options. We trust the designer to utilize their expertise in creating this design.

The content for the business card is included in the attached Word file.

Target Market(s)

Our primary markets are in Africa, China, and Southeast Asian, Latin America, Maldives, Sri Lanka

Industry/Entity Type

Pharmaceutical Manufacturing and Export

Contact Information for Business Card

Colors

Designer to choose colors to be used in the design.

Requirements
Must have
• The reverse side of the business card features solely the logo along with the tagline, "Wellness for All."
Should not have
• The logo should not exceed two instances, encompassing both the front and back sides of the card.

```html
<!DOCTYPE html>
<html lang="en">
<head>
<meta charset="utf-8">
<title>Vexalund Business Card</title>
<link href="https://fonts.googleapis.com/css2?family=Poppins:wght@400;600&family=Karla:wght@300;400&display=swap" rel="stylesheet">
<style>
  :root {
    --backdrop: #2a2a2a;
    --brand-blue: #2596cf;
    --brand-blue-deep: #1f88bf;
    --brand-red: #df523d;
    --paper: #f1f1f1;
    --ink: #2b2b2b;
    --tint: #dcecf6;
  }
  * { margin: 0; padding: 0; box-sizing: border-box; }
  html, body { width: 1200px; height: 1138px; overflow: hidden; background: var(--backdrop); }
  .stage { position: relative; width: 1200px; height: 1138px; }

  .card { position: absolute; border-radius: 19px; overflow: hidden; }

  /* Reverse side */
  .card-back { left: 274px; top: 185px; width: 624px; height: 378px; background: var(--brand-blue); }
  .back-wordmark {
    position: absolute; left: 0; right: 0; top: 124px; text-align: center;
    font-family: "Poppins", sans-serif; font-weight: 600; font-size: 84px; line-height: 1;
    color: var(--paper); letter-spacing: -1px;
  }
  .back-tagline {
    position: absolute; left: 114px; right: 114px; top: 212px;
    display: flex; justify-content: space-between;
    font-family: "Karla", sans-serif; font-weight: 400; font-size: 14px; color: var(--paper);
  }
  .back-web { position: absolute; left: 0; right: 0; top: 337px; height: 16px; }
  .back-web svg { position: absolute; left: 0; top: 0; }
  .back-web-text {
    position: absolute; left: 0; right: 0; top: 0; text-align: center;
    font-family: "Karla", sans-serif; font-weight: 300; font-size: 14px; letter-spacing: 4.5px; color: var(--tint);
  }

  /* Front side */
  .card-front { left: 275px; top: 607px; width: 620px; height: 376px; background: var(--paper); }
  .front-brand { position: absolute; left: 35px; top: 56px; display: flex; align-items: center; gap: 50px; }
  .brand-dot { width: 46px; height: 46px; border-radius: 50%; background: var(--brand-red); }
  .front-wordmark {
    font-family: "Poppins", sans-serif; font-weight: 600; font-size: 52px; line-height: 1;
    color: var(--brand-blue); letter-spacing: -0.5px;
  }
  .person { position: absolute; left: 34px; top: 198px; font-family: "Karla", sans-serif; }
  .person-name { font-family: "Poppins", sans-serif; font-weight: 600; font-size: 24px; color: var(--brand-blue); line-height: 1.2; }
  .person-role { font-size: 15px; color: var(--ink); margin-top: 2px; }
  .address { position: absolute; left: 35px; top: 294px; font-family: "Karla", sans-serif; font-size: 15px; line-height: 22px; color: var(--ink); }

  .contacts { position: absolute; left: 341px; top: 200px; list-style: none; font-family: "Karla", sans-serif; font-size: 15.5px; color: var(--ink); }
  .contacts li { display: flex; align-items: center; height: 22.5px; }
  .contacts svg { width: 14px; height: 14px; margin-right: 13px; flex: none; }

  .footer-band { position: absolute; left: 0; bottom: 0; }
  .footer-tagline {
    position: absolute; left: 335px; top: 341px;
    font-family: "Karla", sans-serif; font-weight: 300; font-size: 15px; color: var(--tint);
  }
</style>
</head>
<body>
<main class="stage">

  <section class="card card-back" aria-label="Card reverse side">
    <div class="back-wordmark">Vexalund</div>
    <div class="back-tagline"><span>W</span><span>E</span><span>L</span><span>L</span><span>N</span><span>E</span><span>S</span><span>S</span><span>&nbsp;</span><span>F</span><span>O</span><span>R</span><span>&nbsp;</span><span>A</span><span>L</span><span>L</span></div>
    <div class="back-web">
      <svg width="624" height="16" viewBox="0 0 624 16">
        <g stroke="#dcecf6" stroke-width="1" fill="none">
          <circle cx="49" cy="8" r="3.5"/>
          <line x1="52.5" y1="8" x2="180" y2="8"/>
          <line x1="444" y1="8" x2="572" y2="8"/>
          <circle cx="575.5" cy="8" r="3.5"/>
        </g>
      </svg>
      <div class="back-web-text">www.vexalund.com</div>
    </div>
  </section>

  <section class="card card-front" aria-label="Card front side">
    <div class="front-brand">
      <div class="brand-dot"></div>
      <div class="front-wordmark">Vexalund</div>
    </div>

    <div class="person">
      <div class="person-name">Arun K. Malvade</div>
      <div class="person-role">CEO, Vexalund</div>
    </div>

    <div class="address">12, Suryodaya Nagar,<br>Nashik-422005 (INDIA)</div>

    <ul class="contacts">
      <li>
        <svg viewBox="0 0 14 14"><path fill="#df523d" d="M1 5c0-2 2-3 6-3s6 1 6 3l-3 1-1-1.5H5L4 6 1 5zm3 1h6l2 6H2l2-6zm3 1.5a2 2 0 1 0 0 4 2 2 0 0 0 0-4z"/></svg>
        +91-9876501234
      </li>
      <li>
        <svg viewBox="0 0 14 14"><rect x="1" y="3" width="12" height="8" fill="#df523d"/><path d="M1 3l6 5 6-5M1 11l4.5-4M13 11 8.5 7" stroke="#f1f1f1" stroke-width="1" fill="none"/></svg>
        amalvade@vexalund.com
      </li>
      <li>
        <svg viewBox="0 0 14 14"><circle cx="7" cy="7" r="5.5" fill="#df523d"/><g stroke="#f1f1f1" stroke-width="0.8" fill="none"><ellipse cx="7" cy="7" rx="2.3" ry="5.5"/><line x1="1.5" y1="7" x2="12.5" y2="7"/><line x1="2.5" y1="4.3" x2="11.5" y2="4.3"/><line x1="2.5" y1="9.7" x2="11.5" y2="9.7"/></g></svg>
        https://vexalund.com
      </li>
    </ul>

    <svg class="footer-band" width="620" height="48" viewBox="0 0 620 48">
      <rect x="0" y="32" width="290" height="16" fill="#df523d"/>
      <path d="M266 48 L288 8 Q292 0 302 0 L620 0 L620 48 Z" fill="#1f88bf"/>
    </svg>
    <div class="footer-tagline">Wellness for All.</div>
  </section>

</main>
</body>
</html>
```